Patent Law

Need to develop a home page for a patent lawyer.

Colors should go with logo, blues...

Company Name- Velun Tresk, PLLC

Company Overview-

I am an Intellectual Property Lawyer and focus on patents, copyrights, trademarks, & trade secrets. I work with small businesses and start ups in the chemical and biotech industries.

Why Us-

I am small firm that can provide large-firm service at a reasonable price. I also can charge flat-fees for entreprenuers in certain practice areas.

Services-
Intellectual Property
Patents
Copyrights
Trademarks
Trade secrets
Healthcare Compliance
Elder law
Wills
Trusts

Website we like-
http://www.quorvantlegal.example/ - within industry!!
http://www.daltrowemiko.example/
http://ulbrixtane.example/
http://thegravelcounsel.example/

Target Market(s)

My customers will be small business, specifically small start-up companies in the chemical and biotech arena.

Industry/Entity Type

Trade

Requirements
Must have
• Colors should go with logo, blues...

```html
<!DOCTYPE html>
<html lang="en">
<head>
<meta charset="utf-8">
<title>Velun Tresk, PLLC — Patent Law Firm</title>
<link rel="stylesheet" href="https://fonts.googleapis.com/css2?family=Figtree:wght@300;400;600;700&display=swap">
<style>
:root{
  --blue:#1a8ad8;
  --blue-bright:#0f94e6;
  --ink:#1b1b1b;
  --body:#4a4a4a;
  --muted:#8a8a8a;
  --page:#f3f3f3;
  --page-light:#fafafa;
  --page-shade:#e6e6e6;
  --white:#ffffff;
  --hero-warm:#8a6236;
  --hero-deep:#2a1d12;
}
*{box-sizing:border-box;margin:0;padding:0}
html,body{width:1200px;height:1001px;overflow:hidden}
body{font-family:"Figtree",Arial,sans-serif;background:var(--page);color:var(--body);position:relative}
.abs{position:absolute}

/* hero */
.hero{position:absolute;left:0;top:0;width:1200px;height:462px;overflow:hidden}
.hero-photo{position:absolute;inset:0;background:linear-gradient(120deg,#b98a4c 0%,var(--hero-warm) 30%,#5a3e22 55%,var(--hero-deep) 100%)}
.hero svg{position:absolute;inset:0}
.brand{left:240px;top:10px;width:140px;text-align:center;color:var(--white)}
.brand-mark{width:46px;height:46px;border-radius:50%;background:var(--blue);margin:0 auto 12px}
.brand-name{font-size:14px;font-weight:600;letter-spacing:.5px}
.nav{left:412px;top:72px;display:flex;gap:8px}
.nav a{color:var(--white);text-decoration:none;font-size:12px;padding:4px 7px;margin-right:14px}
.nav a.active{background:var(--blue-bright);border-radius:2px}
.locator{left:764px;top:0;width:178px;height:140px;border:2px solid var(--blue-bright);border-top:0;background:var(--blue-bright)}
.locator-map{height:97px;background:linear-gradient(135deg,#e5e3dc,#d7d6cf 60%,#c9d7e6)}
.locator-body{padding:3px 3px;color:var(--white)}
.locator-ask{font-size:10px;color:#cfe8fb}
.locator-ask span{color:var(--white)}
.locator-row{display:flex;align-items:center;margin-top:2px;font-size:9px}
.locator-phone{font-size:14px;font-weight:700;margin-right:8px}
.locator-row svg{margin:0 3px 0 12px}
.hero-title{right:265px;top:218px;text-align:right;color:var(--white)}
.hero-title h1{font-size:42px;font-weight:700;line-height:1.1}
.hero-title h2{font-size:29px;font-weight:300;line-height:1}
.hero-text{right:265px;top:306px;width:350px;text-align:right;color:var(--white);font-size:11px;line-height:13.5px}

/* page */
.page-shape{left:0;top:462px}
.cols{top:498px;left:0;width:1200px}
.col{position:absolute;text-align:center}
.col h3{font-size:15px;font-weight:700;color:var(--ink);letter-spacing:.3px}
.col .tag{font-size:11px;font-style:italic;color:var(--muted);margin-bottom:12px}
.col p{font-size:8.5px;line-height:13px;color:var(--body)}
.divider-shadow{left:200px;top:648px;width:770px;height:10px;background:radial-gradient(ellipse at center top,rgba(0,0,0,.18),rgba(0,0,0,0) 70%)}
.portrait{left:316px;top:706px;width:140px;height:164px;border:2px solid #d2d2d2;background:linear-gradient(180deg,#f2f2f2,#d6d2cc 60%,#b59a7c)}
.rule-v{left:488px;top:706px;width:1px;height:166px;background:#d6d6d6}
.intro{left:525px;top:700px}
.intro h2{font-size:27px;font-weight:300;color:var(--blue);letter-spacing:.3px}
.intro p{font-size:14px;line-height:19px;color:var(--body);width:380px;margin-top:6px}
.hours{display:flex;gap:22px;margin-top:12px;font-size:11px;align-items:baseline}
.hours b{font-size:14px;color:var(--blue);font-weight:700}
.btn{display:inline-block;margin-top:20px;background:linear-gradient(var(--blue-bright),#0a7cc6);color:var(--white);font-size:14px;font-weight:700;padding:11px 18px;border-radius:2px;text-decoration:none}
.footer-rule{left:234px;top:926px;width:731px;height:1px;background:#cfcfcf}
.copyright{left:290px;top:963px;font-size:9px;color:var(--body)}
.footer-nav{left:516px;top:964px;display:flex;font-size:9.5px}
.footer-nav a{color:var(--body);text-decoration:none;padding:0 11px;border-left:1px solid #999}
.footer-nav a:first-child{border-left:0;color:var(--blue)}
.base-bar{left:0;top:996px;width:1200px;height:5px;background:var(--blue-bright)}
</style>
</head>
<body>

<header class="hero">
  <div class="hero-photo" role="img" aria-label="Scales of justice on a desk in a wood-panelled courtroom"></div>
  <svg width="1200" height="462" aria-hidden="true">
    <polygon points="418,0 1200,0 1200,462 668,462" fill="#1c140d" opacity=".72"/>
    <polygon points="418,0 520,0 920,462 668,462" fill="#000" opacity=".12"/>
  </svg>

  <div class="abs brand">
    <div class="brand-mark"></div>
    <div class="brand-name">VELUN TRESK, PLLC</div>
  </div>

  <nav class="abs nav">
    <a href="#" class="active">Home</a>
    <a href="#">About</a>
    <a href="#">Resources</a>
    <a href="#">Practice Areas</a>
  </nav>

  <aside class="abs locator">
    <div class="locator-map" role="img" aria-label="Street map showing the office location"></div>
    <div class="locator-body">
      <div class="locator-ask">Any Questions? <span>Please Call</span></div>
      <div class="locator-row">
        <span class="locator-phone">888-555-0142</span> OR
        <svg width="12" height="9" viewBox="0 0 12 9"><rect x=".5" y=".5" width="11" height="8" fill="#fff"/><path d="M.5 .5 6 5 11.5 .5" stroke="#0f94e6" fill="none"/></svg>
        Mail Us
      </div>
    </div>
  </aside>

  <div class="abs hero-title">
    <h1>Velun Tresk</h1>
    <h2>Paten Law Firm</h2>
  </div>
  <p class="abs hero-text">I am an Intellectual Property Lawyer and focus on patents, copyrights, trademarks, &amp; trade secrets. I work with small businesses and start ups in the chemical and biotech industries.</p>
</header>

<svg class="abs page-shape" width="320" height="539" aria-hidden="true">
  <polygon points="0,0 12,0 305,539 0,539" fill="var(--page-shade)"/>
  <polygon points="0,60 0,539 245,539" fill="#e9e9e9"/>
</svg>

<section class="abs cols">
  <div class="col" style="left:272px;width:200px">
    <h3>WHY US?</h3>
    <div class="tag">This is a reason why you choose us</div>
    <p>I am small firm that can provide large-firm service at a reasonable price. I also can charge flat-fees for entreprenuers in certain practice areas.</p>
  </div>
  <div class="col" style="left:526px;width:210px">
    <h3>WHAT WE DO</h3>
    <div class="tag">What can we do for you?</div>
    <p>Intellectual Property &nbsp; I &nbsp; Patents &nbsp; I &nbsp;Copyrights<br>Trademarks &nbsp; I &nbsp; Trade secrets &nbsp; I &nbsp; Healthcare<br>Compliance &nbsp; I &nbsp; Elder law &nbsp; I &nbsp; Wills &nbsp; I &nbsp; Trusts</p>
  </div>
  <div class="col" style="left:779px;width:160px">
    <h3>CONTACT INFO</h3>
    <div class="tag">Where you can find us?</div>
    <p>48 Larkfield Rd. - Oak Square<br>BRENTVALE - OHIO 44120<br><br>Phone. 888-555-0142<br>Email. client@veluntresk.example</p>
  </div>
</section>

<div class="abs divider-shadow"></div>

<div class="abs portrait" role="img" aria-label="Portrait photo of the attorney"></div>
<div class="abs rule-v"></div>

<section class="abs intro">
  <h2>Velun Tresk - Patent Lawyer.</h2>
  <p>For business consultation and information of your patents, please contact us. We are ready to serve you.</p>
  <div class="hours">
    <span>Open <b>08am - 16pm</b></span>
    <span>Appointment <b>888-555-0142</b></span>
  </div>
  <a href="#" class="btn">SEND US EMAIL</a>
</section>

<div class="abs footer-rule"></div>
<footer>
  <div class="abs copyright">Velun Tresk | © 2014 All Right Reserved</div>
  <nav class="abs footer-nav">
    <a href="#">Home</a><a href="#">Pricing</a><a href="#">Resource</a><a href="#">Terms &amp; Condition</a><a href="#">Privacy Policy</a><a href="#">Fees</a>
  </nav>
</footer>
<div class="abs base-bar"></div>

</body>
</html>
```